Quorva - corporate Business Card

We need a good look and innovative business card for a new start up company based in Los Angeles called "Quorva". We are in a payment business, including payment card, app, and ewallet. We are expert in online payment and Card not present (CNP) transaction.
We need an innovative, modern business card.

Our logo font is Aero Matics

Target Market(s)

Startup - Bank - Online Payment - Card Manufacturing

Industry/Entity Type

Startup

Contact Information for Business Card

phone: 555 014 7396 - Address: 4172 Marlowe blvd, Ashvale City, CA 90299

Requirements
Must have
• Message: innovative, professional, expert, high tech, trust, online payment expert, security
Nice to have
• no comment
Should not have
• no Comment

```html
<!DOCTYPE html>
<html lang="en">
<head>
<meta charset="utf-8">
<title>Quorva – Business Card</title>
<link href="https://fonts.googleapis.com/css2?family=Lato:wght@400;700&display=swap" rel="stylesheet">
<style>
  :root {
    --brand-red: #b01c2e;
    --ink-dark: #2a2a2a;
    --ink-grey: #707070;
    --blush: #f6ece9;
    --card-white: #ffffff;
    --backdrop: #e4e2e2;
  }
  * { box-sizing: border-box; margin: 0; padding: 0; }
  html, body { width: 1200px; height: 900px; overflow: hidden; }
  body {
    background: var(--backdrop);
    font-family: 'Lato', sans-serif;
    position: relative;
  }
  .card {
    position: absolute;
    width: 600px;
    height: 343px;
    background: var(--card-white);
    border-radius: 18px;
    overflow: hidden;
    box-shadow: 0 6px 18px rgba(0,0,0,0.12);
  }
  .card--front { left: 300px; top: 90px; }
  .card--back { left: 300px; top: 470px; }

  .blush-disc {
    position: absolute;
    border-radius: 50%;
    background: var(--blush);
  }
  .card--front .blush-disc { width: 300px; height: 300px; left: 150px; top: 22px; }
  .card--back .blush-disc { width: 230px; height: 230px; left: 470px; top: 90px; }

  .wordmark {
    position: absolute;
    display: flex;
    align-items: center;
    gap: 12px;
    color: var(--brand-red);
    font-weight: 700;
    letter-spacing: 1px;
    line-height: 1;
  }
  .wordmark__dot {
    border-radius: 50%;
    background: var(--brand-red);
    flex: none;
  }
  .card--front .wordmark { left: 160px; top: 142px; font-size: 58px; }
  .card--front .wordmark__dot { width: 66px; height: 66px; }
  .card--back .wordmark { left: 40px; top: 96px; font-size: 44px; }
  .card--back .wordmark__dot { width: 52px; height: 52px; }

  .web-address {
    position: absolute;
    left: 300px; top: 240px;
    font-size: 14px;
    color: var(--brand-red);
  }

  .holder {
    position: absolute;
    right: 44px; top: 34px;
    text-align: right;
  }
  .holder__name { color: var(--brand-red); font-size: 19px; font-weight: 700; }
  .holder__role { color: var(--ink-dark); font-size: 13px; margin-top: 2px; }

  .contact {
    position: absolute;
    left: 44px; top: 190px;
    font-size: 13px;
    color: var(--ink-grey);
    line-height: 1.45;
  }
  .contact__label { color: var(--brand-red); font-weight: 700; }
  .contact__list { list-style: none; margin-top: 12px; }
  .contact__list li { display: flex; align-items: center; gap: 8px; }
  .contact__list svg { width: 12px; height: 12px; fill: var(--brand-red); flex: none; }
</style>
</head>
<body>
  <section class="card card--front">
    <div class="blush-disc"></div>
    <div class="wordmark"><span class="wordmark__dot"></span>quorva</div>
    <div class="web-address">www.quorva.com</div>
  </section>

  <section class="card card--back">
    <div class="blush-disc"></div>
    <div class="holder">
      <div class="holder__name">Dana Reyes</div>
      <div class="holder__role">President</div>
    </div>
    <div class="wordmark"><span class="wordmark__dot"></span>quorva</div>
    <div class="contact">
      <div class="contact__label">Address:</div>
      <div>4172 Marlowe blvd</div>
      <div>Ashvale City, CA 90299</div>
      <ul class="contact__list">
        <li><svg viewBox="0 0 24 24"><path d="M6.6 10.8a15 15 0 0 0 6.6 6.6l2.2-2.2a1 1 0 0 1 1-.25 11.4 11.4 0 0 0 3.6.57 1 1 0 0 1 1 1V20a1 1 0 0 1-1 1A17 17 0 0 1 3 4a1 1 0 0 1 1-1h3.5a1 1 0 0 1 1 1c0 1.25.2 2.45.57 3.57a1 1 0 0 1-.25 1z"/></svg>555 014 7396</li>
        <li><svg viewBox="0 0 24 24"><path d="M2 5h20v14H2z M2 5l10 8 10-8" fill="none" stroke="#b01c2e" stroke-width="2.4"/></svg>info@quorva.com</li>
        <li><svg viewBox="0 0 24 24"><circle cx="12" cy="12" r="10" fill="none" stroke="#b01c2e" stroke-width="2.4"/><path d="M2 12h20M12 2c3 3 3 17 0 20M12 2c-3 3-3 17 0 20" fill="none" stroke="#b01c2e" stroke-width="2"/></svg>www.quorva.com</li>
      </ul>
    </div>
  </section>
</body>
</html>
```